Fine Art business needs new website

We need a simple website with a home page, about us page, New sculptures, Sold sculptures, and a contact us page.Our sculptures are very high end one of a kind pieces. As such we need the site to be VERY elegant and professional. Lastly, because I'll be updating pictures on the website on a monthly basis it needs to be user friendly to update (Wordpress is preferred). The only branding we have so far for the business is a business card.
Updates
I wasn't completely ready when this project launched, also I am on the road right now and haven't been able to be as responsive to all you designers as I would like. I will work on giving feedback to all the top designs we've received so far. Thank you all so much for your participation and hardwork.
Target Market(s)
High end customers (affluent), art collectors, interior decorators/designers
Industry/Entity Type
Art Gallery
Coding
Coded - Design and coding required
Number of Pages Required
5+ page
Requirements
Must have
- Easily editable picture gallery for myself so that I can add new pieces(pictures of the pieces), remove sold pieces, etc. I would like the website to be built in wordpress so I can update it. I currently use mangewordpress through Netmarro for my other business website and would like to do the same for this one.
- Pages:
- -Intro page with featured pieces
- -Current pieces gallery (for sale) mainly a picture gallery
- -Sculptures archive (sold pieces) another picture gallery
- -About us: Pull-down of -about the artist (attached content)
- -Artistic Process (attached content)
- -Show Schedule:
- -one page dedicated to "friends of TMV" (basically a link page)
- TO BE CLEAR "www.pineroverslane.com" IS A TOTALLY DIFFERENT SITE AND I'M NOT TRYING TO COMBINE THE TWO OR JOIN THEM INTO ONE. This page needs be more elegant and seperate from the Pine Rovers site.
- UPDATE: I'd like a link to the TMV Facebook page: https://www.faceplume-social.com/mirelcraftworks/
Nice to have
- I would like the pictures on the gallery pages able to have text connected with them (Materials, price)
- I would like the site style and fonts to be similar to our business cards we've already had designed (picture attached).
Should not have
- Too much flash or other things that will make the site slow to load.

```html
<!DOCTYPE html>
<html lang="en">
<head>
<meta charset="utf-8">
<title>Mirel Art Studio — New Sculptures</title>
<link href="https://fonts.googleapis.com/css2?family=Cinzel:wght@400;600&family=Poppins:wght@300;400;500;600&display=swap" rel="stylesheet">
<style>
:root{
  --purple:#5a1596;
  --purple-dark:#3b0d63;
  --ink:#222222;
  --muted:#666666;
  --line:#e3e3e3;
  --badge:#e0202a;
  --card-bg:#ffffff;
  --dot-1:#5a1596;
  --dot-2:#b8327a;
  --dot-3:#d8312b;
  --dot-4:#2a6fb5;
}
*{box-sizing:border-box;margin:0;padding:0}
html,body{width:1200px;height:2696px;overflow:hidden}
body{background:#fff;font-family:'Poppins',sans-serif;color:var(--ink);position:relative}

/* header */
.site-header{position:absolute;top:0;left:0;width:1200px;height:188px}
.contact-info{position:absolute;left:112px;top:10px;font-size:12px;color:var(--muted);line-height:34px}
.contact-info div{display:flex;align-items:center;gap:12px}
.contact-info svg{width:14px;height:14px}
.brand{position:absolute;left:50%;transform:translateX(-50%);display:flex;flex-direction:column;align-items:center;gap:14px;width:400px}
.site-header .brand{top:66px}
.brand-mark{width:56px;height:56px;border-radius:50%;background:var(--purple)}
.brand-name{font-family:'Cinzel',serif;font-weight:600;font-size:16px;letter-spacing:3px;color:var(--purple-dark)}
.social{display:flex;gap:28px}
.site-header .social{position:absolute;right:96px;top:10px}
.social span{width:32px;height:32px;border-radius:50%;display:block}
.social span:nth-child(1){background:var(--dot-1)}
.social span:nth-child(2){background:var(--dot-2)}
.social span:nth-child(3){background:var(--dot-3)}
.social span:nth-child(4){background:var(--dot-4)}

.main-nav{position:absolute;top:188px;left:0;width:1200px;height:42px;border-top:1px solid var(--line);border-bottom:1px solid var(--line);display:flex;justify-content:center;align-items:center;gap:64px;font-size:11px;letter-spacing:.5px;text-transform:uppercase;color:#333}
.main-nav svg{width:13px;height:13px}

/* hero */
.hero{position:absolute;top:232px;left:0;width:1200px;height:328px;background:radial-gradient(ellipse at 20% 40%,#8a5ab8 0%,transparent 40%),radial-gradient(ellipse at 80% 60%,#7c4aa8 0%,transparent 45%),linear-gradient(135deg,#2a0f40 0%,#5b2e82 35%,#3a1656 65%,#21102f 100%);display:flex;align-items:center;justify-content:center;padding-top:12px}
.hero-title{font-family:'Cinzel',serif;font-weight:400;font-size:64px;color:#fff;letter-spacing:1px}

/* gallery */
.section-title{position:absolute;top:660px;left:0;width:1200px;text-align:center;font-family:'Cinzel',serif;font-weight:400;font-size:44px;line-height:56px;color:#2a2a2a}
.gallery{position:absolute;top:752px;left:100px;width:1000px;display:grid;grid-template-columns:repeat(3,324px);column-gap:14px;row-gap:32px}
.card{background:var(--card-bg);box-shadow:0 4px 14px rgba(0,0,0,.12)}
.card-photo{position:relative;height:280px;background:#111}
.badge{position:absolute;top:14px;left:14px;background:var(--badge);color:#fff;font-size:9px;font-weight:500;padding:4px 10px;border-radius:2px;text-transform:uppercase}
.card-info{height:108px;display:flex;align-items:center;justify-content:space-between;padding:0 22px 0 18px}
.card-name{font-size:15px;font-weight:500;color:#222}
.card-price{font-size:13px;color:var(--muted);margin-top:4px}
.btn{background:var(--purple);color:#fff;font-size:12px;font-weight:500;text-transform:uppercase;display:inline-flex;align-items:center;justify-content:center}
.card-info .btn{width:116px;height:40px}
.view-all{position:absolute;top:2066px;left:520px;width:160px;height:48px;font-size:13px}

/* footer */
.site-footer{position:absolute;top:2170px;left:0;width:1200px;height:526px;background:#fff;text-align:center}
.site-footer .brand{top:54px}
.footer-title{position:absolute;top:176px;left:0;width:100%;font-family:'Cinzel',serif;font-weight:400;font-size:24px;color:#2a2a2a}
.footer-text{position:absolute;top:218px;left:380px;width:440px;font-size:12px;line-height:20px;color:var(--muted)}
.subscribe{position:absolute;top:296px;left:368px;display:flex}
.subscribe-input{width:324px;height:42px;border:1px solid #d5d5d5;background:#fff;font-size:12px;color:#999;padding:0 14px;display:flex;align-items:center}
.subscribe .btn{width:136px;height:42px;background:var(--purple-dark)}
.site-footer .social{position:absolute;top:368px;left:50%;transform:translateX(-50%);gap:28px}
.copyright{position:absolute;top:490px;left:0;width:100%;font-size:11px;color:#888}
</style>
</head>
<body>

<header class="site-header">
  <div class="contact-info">
    <div><svg viewBox="0 0 24 24"><path fill="#777" d="M6.6 10.8a15 15 0 0 0 6.6 6.6l2.2-2.2c.3-.3.7-.4 1-.2 1.1.4 2.3.6 3.6.6.6 0 1 .4 1 1V20c0 .6-.4 1-1 1A17 17 0 0 1 3 4c0-.6.4-1 1-1h3.5c.6 0 1 .4 1 1 0 1.3.2 2.5.6 3.6.1.3 0 .7-.2 1z"/></svg>(555) 010-2384</div>
    <div><svg viewBox="0 0 24 24"><rect x="2" y="5" width="20" height="14" rx="2" fill="none" stroke="#777" stroke-width="2"/><path d="M3 6l9 7 9-7" fill="none" stroke="#777" stroke-width="2"/></svg>info@mirelartstudio.com</div>
  </div>
  <div class="brand">
    <span class="brand-mark"></span>
    <span class="brand-name">MIREL ART STUDIO</span>
  </div>
  <div class="social"><span></span><span></span><span></span><span></span></div>
</header>

<nav class="main-nav">
  <span>Home</span><span>About Us</span><span>New Sculptures</span><span>Sold Sculptures</span><span>Contact Us</span>
  <svg viewBox="0 0 24 24"><circle cx="10" cy="10" r="6" fill="none" stroke="#333" stroke-width="2.5"/><path d="M15 15l6 6" stroke="#333" stroke-width="2.5"/></svg>
</nav>

<section class="hero" role="img" aria-label="Close-up photograph of purple amethyst crystals">
  <h1 class="hero-title">NEW SCULPTURES</h1>
</section>

<h2 class="section-title">NEW SCULPTURE</h2>

<main class="gallery">
  <article class="card"><div class="card-photo" role="img" aria-label="Amber and orange stone sculpture" style="background:radial-gradient(circle at 50% 50%,#b8662a 0%,#5a2a10 35%,#0d0d0d 70%)"><span class="badge">For Sale</span></div><div class="card-info"><div><div class="card-name">SCULPTURE~1</div><div class="card-price">$0.00</div></div><span class="btn">Buy Now</span></div></article>
  <article class="card"><div class="card-photo" role="img" aria-label="Green malachite stone sculpture" style="background:radial-gradient(circle at 50% 50%,#2f6e55 0%,#173a2e 35%,#0d0d0d 70%)"><span class="badge">Available</span></div><div class="card-info"><div><div class="card-name">SCULPTURE~1</div><div class="card-price">$0.00</div></div><span class="btn">Buy Now</span></div></article>
  <article class="card"><div class="card-photo" role="img" aria-label="Golden agate slice sculpture" style="background:radial-gradient(circle at 50% 50%,#c7862e 0%,#6a3e12 35%,#0d0d0d 70%)"><span class="badge">Available</span></div><div class="card-info"><div><div class="card-name">SCULPTURE~1</div><div class="card-price">$0.00</div></div><span class="btn">Buy Now</span></div></article>
  <article class="card"><div class="card-photo" role="img" aria-label="Bronze spiral shell sculpture" style="background:radial-gradient(circle at 50% 50%,#9a7638 0%,#4a3618 35%,#0d0d0d 70%)"><span class="badge">For Sale</span></div><div class="card-info"><div><div class="card-name">SCULPTURE~1</div><div class="card-price">$0.00</div></div><span class="btn">Buy Now</span></div></article>
  <article class="card"><div class="card-photo" role="img" aria-label="Rose brown carved stone sculpture" style="background:radial-gradient(circle at 50% 50%,#8a5a48 0%,#42281f 35%,#0d0d0d 70%)"><span class="badge">Available</span></div><div class="card-info"><div><div class="card-name">SCULPTURE~1</div><div class="card-price">$0.00</div></div><span class="btn">Buy Now</span></div></article>
  <article class="card"><div class="card-photo" role="img" aria-label="Purple geode slab sculpture" style="background:radial-gradient(circle at 50% 50%,#6d3aa0 0%,#3a1c55 35%,#0d0d0d 70%)"><span class="badge">For Sale</span></div><div class="card-info"><div><div class="card-name">SCULPTURE~1</div><div class="card-price">$0.00</div></div><span class="btn">Buy Now</span></div></article>
  <article class="card"><div class="card-photo" role="img" aria-label="Blue twisted stone sculpture" style="background:radial-gradient(circle at 50% 50%,#3a56a0 0%,#1c2852 35%,#0d0d0d 70%)"><span class="badge">Available</span></div><div class="card-info"><div><div class="card-name">SCULPTURE~1</div><div class="card-price">$0.00</div></div><span class="btn">Buy Now</span></div></article>
  <article class="card"><div class="card-photo" role="img" aria-label="Amethyst cluster sculpture" style="background:radial-gradient(circle at 50% 50%,#5a3c9a 0%,#2c1c4e 35%,#0d0d0d 70%)"><span class="badge">For Sale</span></div><div class="card-info"><div><div class="card-name">SCULPTURE~1</div><div class="card-price">$0.00</div></div><span class="btn">Buy Now</span></div></article>
  <article class="card"><div class="card-photo" role="img" aria-label="Pale crystal geode sculpture" style="background:radial-gradient(circle at 50% 50%,#8a90a8 0%,#3e4256 35%,#0d0d0d 70%)"><span class="badge">Available</span></div><div class="card-info"><div><div class="card-name">SCULPTURE~1</div><div class="card-price">$0.00</div></div><span class="btn">Buy Now</span></div></article>
</main>

<span class="btn view-all">View All</span>

<footer class="site-footer">
  <div class="brand">
    <span class="brand-mark"></span>
    <span class="brand-name">MIREL ART STUDIO</span>
  </div>
  <h3 class="footer-title">Get In Touch With Us</h3>
  <p class="footer-text">Visit the studio or leave your email to hear first when new one of a kind pieces arrive.</p>
  <div class="subscribe">
    <div class="subscribe-input">Enter Your Email Address</div>
    <span class="btn">Subscribe</span>
  </div>
  <div class="social"><span></span><span></span><span></span><span></span></div>
  <p class="copyright">© Copyright 2018 Mirel Art Studio. All Rights Reserved.</p>
</footer>

</body>
</html>
```